BRIGHT RIVER POWER.

I'd like my business logo.
contact name: Dennis Halvorsen
phone:0438759164
email: info@brightriverpower.net.au
website: www.brightriverpower.net.au

services:
solar
battery storage
LED lighting
energy saving solutions
general electrical
I'd like the design to look professional

Target Market(s)

Everyone

Industry/Entity Type

Business

Contact Information for Business Card

as described above

Requirements
Must have
• Id like the colours and the design to work well with my logo.

```html
<!DOCTYPE html>
<html lang="en">
<head>
<meta charset="utf-8">
<title>Bright River Power – Business Card</title>
<link rel="stylesheet" href="https://fonts.googleapis.com/css2?family=Source+Sans+3:wght@400;600&display=swap">
<style>
  :root {
    --backdrop: #4a4a4a;
    --card-white: #ffffff;
    --brand-green: #3f9c35;
    --brand-green-light: #8fc73e;
    --brand-green-deep: #3a9a32;
    --brand-orange: #f5a623;
    --sun-tint: #fdf1dc;
    --text-dark: #555555;
    --text-white: #ffffff;
  }
  * { box-sizing: border-box; margin: 0; padding: 0; }
  html, body { width: 1105px; height: 1200px; overflow: hidden; }
  body {
    background: var(--backdrop);
    font-family: "Source Sans 3", "Myriad Pro", Arial, sans-serif;
    position: relative;
  }
  .card {
    position: absolute;
    left: 193px;
    width: 720px;
    height: 410px;
    box-shadow: 0 4px 10px rgba(0,0,0,0.45);
    overflow: hidden;
  }
  /* Front */
  .card-front { top: 167px; background: var(--card-white); }
  .front-decoration {
    position: absolute;
    right: -70px;
    top: 60px;
    width: 380px;
    height: 380px;
    border-radius: 50%;
    background: radial-gradient(circle, #f4f9ee 0%, var(--sun-tint) 70%, rgba(255,255,255,0) 71%);
    opacity: 0.7;
  }
  .brand-front {
    position: absolute;
    left: 70px;
    top: 100px;
    display: flex;
    align-items: center;
    gap: 12px;
  }
  .brand-mark {
    width: 44px;
    height: 44px;
    border-radius: 50%;
    background: var(--brand-orange);
    flex: none;
  }
  .brand-name {
    font-weight: 600;
    font-size: 38px;
    letter-spacing: 1px;
    color: var(--brand-green);
    line-height: 1;
  }
  .contact-band {
    position: absolute;
    left: 87px;
    top: 157px;
    width: 58px;
    bottom: 0;
    background: linear-gradient(to bottom, var(--brand-green-light), var(--brand-green));
  }
  .contact-icon {
    position: absolute;
    left: 50%;
    transform: translateX(-50%);
    fill: var(--text-white);
  }
  .icon-person { top: 62px; }
  .icon-phone { top: 113px; }
  .icon-mail { top: 142px; }
  .icon-globe { top: 167px; }
  .contact-name {
    position: absolute;
    left: 186px;
    top: 216px;
    font-size: 27px;
    font-weight: 600;
    color: var(--brand-green);
  }
  .contact-lines {
    position: absolute;
    left: 188px;
    top: 266px;
    list-style: none;
    font-size: 20px;
    line-height: 27px;
    color: var(--text-dark);
  }
  /* Back */
  .card-back {
    top: 623px;
    background: radial-gradient(ellipse at 50% 40%, #95c93c 0%, #6fb236 40%, var(--brand-green-deep) 85%);
    color: var(--text-white);
    text-align: center;
  }
  .brand-back {
    position: absolute;
    left: 0; right: 0;
    top: 128px;
    display: flex;
    justify-content: center;
    align-items: center;
    gap: 14px;
  }
  .brand-back .brand-mark { background: var(--text-white); width: 48px; height: 48px; }
  .brand-back .brand-name { color: var(--text-white); font-size: 46px; }
  .services {
    position: absolute;
    left: 0; right: 0;
    top: 316px;
    font-size: 21px;
    line-height: 28px;
  }
  .services .dot { margin: 0 6px; }
</style>
</head>
<body>
  <section class="card card-front">
    <div class="front-decoration" role="img" aria-label="Faint brand emblem decoration"></div>
    <div class="brand-front">
      <span class="brand-mark"></span>
      <span class="brand-name">BRIGHT RIVER POWER</span>
    </div>
    <div class="contact-band">
      <svg class="contact-icon icon-person" width="24" height="24" viewBox="0 0 24 24"><circle cx="12" cy="7" r="5"/><path d="M2 23c0-6 4-9 10-9s10 3 10 9z"/></svg>
      <svg class="contact-icon icon-phone" width="18" height="18" viewBox="0 0 24 24"><path d="M6.6 10.8a15 15 0 0 0 6.6 6.6l2.2-2.2a1 1 0 0 1 1-.25 11 11 0 0 0 3.6.6 1 1 0 0 1 1 1V20a1 1 0 0 1-1 1A17 17 0 0 1 3 4a1 1 0 0 1 1-1h3.5a1 1 0 0 1 1 1 11 11 0 0 0 .6 3.6 1 1 0 0 1-.25 1z"/></svg>
      <svg class="contact-icon icon-mail" width="18" height="14" viewBox="0 0 24 18"><path d="M1 1h22v16H1z" fill="none" stroke="#fff" stroke-width="2"/><path d="M1 1l11 9 11-9" fill="none" stroke="#fff" stroke-width="2"/></svg>
      <svg class="contact-icon icon-globe" width="18" height="18" viewBox="0 0 24 24"><circle cx="12" cy="12" r="10" fill="none" stroke="#fff" stroke-width="2.5"/><ellipse cx="12" cy="12" rx="4" ry="10" fill="none" stroke="#fff" stroke-width="2"/><path d="M2 12h20" stroke="#fff" stroke-width="2"/></svg>
    </div>
    <h1 class="contact-name">Dennis Halvorsen</h1>
    <ul class="contact-lines">
      <li>0438759164</li>
      <li>info@brightriverpower.net.au</li>
      <li>brightriverpower.net.au</li>
    </ul>
  </section>

  <section class="card card-back">
    <div class="brand-back">
      <span class="brand-mark"></span>
      <span class="brand-name">BRIGHT RIVER POWER</span>
    </div>
    <p class="services">
      Solar<span class="dot">•</span>Battery storage<span class="dot">•</span>LED lighting<br>
      Energy saving solutions
    </p>
  </section>
</body>
</html>
```